Brookmere Osteopathy flyer

I want a clean clear DL flyer (but also want an A4 poster) promoting a new Osteopathic business in a semi rural area in Tasmania (Australia).
It can have pictures like the examples attached to show people what Osteopathy is (its like Chiropractic and physiotherapy).
I am the sole practioner and am male, so any pictures would be best to be a white male if possible.
I've attached some wording, you can use all, or none of it
I don't have a phone number for the business yet
info@brookmereosteopathy.example
www.brookmereosteopathy.example
Target Market(s)
Australians, from tradies, professionals, babies to retired people
Industry/Entity Type
Health
Look and feel

```html
<!DOCTYPE html>
<html lang="en">
<head>
<meta charset="utf-8">
<title>Brookmere Osteopathy – Flyer</title>
<link rel="stylesheet" href="https://fonts.googleapis.com/css2?family=Poppins:ital,wght@0,400;0,500;0,600;0,700;0,800;1,400;1,600;1,700&family=Playfair+Display:ital,wght@1,500&display=swap">
<style>
  :root {
    --blue: #0e8fd2;
    --blue-deep: #0b6fae;
    --blue-sky: #2fb3e8;
    --navy: #0d3a66;
    --navy-text: #12406e;
    --orange: #f7923a;
    --white: #ffffff;
    --ink: #1e1e1e;
    --pale: #eef6fc;
  }
  * { margin: 0; padding: 0; box-sizing: border-box; }
  html, body { width: 678px; height: 1200px; overflow: hidden; background: var(--white); }
  .flyer {
    position: relative; width: 678px; height: 1200px; overflow: hidden;
    background: linear-gradient(180deg, var(--white) 0%, var(--pale) 45%, var(--white) 100%);
    font-family: "Poppins", sans-serif;
  }
  .shape { position: absolute; left: 0; top: 0; }
  .brand-badge {
    position: absolute; left: 258px; top: 36px; width: 164px; height: 164px;
    border-radius: 50%; background: var(--white);
    box-shadow: 0 4px 12px rgba(0,0,0,.18);
    display: flex; align-items: center; justify-content: center; text-align: center;
  }
  .brand-name {
    font-family: "Poppins", sans-serif; font-weight: 600; font-size: 17px;
    line-height: 1.25; color: var(--blue);
  }
  .headline-main {
    position: absolute; left: 0; width: 678px; text-align: center;
    top: 214px; font-weight: 800; font-size: 72px; line-height: 1;
    color: var(--blue); letter-spacing: -0.5px;
  }
  .headline-script {
    position: absolute; top: 272px; left: 203px; white-space: nowrap;
    font-family: "Playfair Display", serif; font-style: italic;
    font-weight: 500; font-size: 56px; line-height: 1; color: var(--orange);
  }
  .photo {
    position: absolute; width: 190px; height: 190px; border-radius: 50%;
    border: 9px solid var(--blue); background: var(--white);
  }
  .photo-fill { width: 100%; height: 100%; border-radius: 50%; border: 4px solid var(--white); }
  .photo-head { left: 44px; top: 362px; }
  .photo-head .photo-fill { background: radial-gradient(circle at 45% 45%, #e8c6b0 0%, #c99c85 40%, #dfe3ec 75%); }
  .photo-baby { left: 250px; top: 342px; }
  .photo-baby .photo-fill { background: radial-gradient(circle at 50% 40%, #f0d2c2 0%, #d8b3a6 35%, #6fb4da 70%, #c9c6d4 100%); }
  .photo-back { left: 456px; top: 362px; }
  .photo-back .photo-fill { background: radial-gradient(circle at 45% 50%, #e4b79a 0%, #cf9a7a 50%, #e9ebef 90%); }
  .section-title {
    position: absolute; left: 0; top: 588px; width: 678px; text-align: center;
    font-weight: 700; font-size: 34px; line-height: 1.1;
  }
  .section-title .line-one { color: var(--navy-text); display: block; }
  .section-title .line-two { color: var(--white); display: block; }
  .divider {
    position: absolute; left: 50px; top: 678px; width: 590px; height: 1px;
    background: linear-gradient(90deg, rgba(255,255,255,.8) 0 35%, var(--orange) 35% 67%, rgba(255,255,255,.8) 67% 100%);
  }
  .reasons {
    position: absolute; left: 30px; width: 620px; display: grid;
    grid-template-columns: repeat(5, 1fr); text-align: center;
  }
  .reasons-row-one { top: 700px; }
  .reasons-row-two { top: 822px; }
  .reason { display: flex; flex-direction: column; align-items: center; }
  .reason-icon {
    width: 70px; height: 70px; border-radius: 50%; border: 2px solid var(--white);
    background: radial-gradient(circle at 50% 45%, rgba(255,255,255,.55) 0%, rgba(255,255,255,.28) 38%, rgba(255,255,255,.06) 70%);
    margin-bottom: 6px;
  }
  .reason-label {
    color: var(--white); font-weight: 500; font-size: 15px; line-height: 17px; white-space: nowrap;
  }
  .info-band {
    position: absolute; left: 0; top: 981px; width: 678px; height: 116px; background: var(--navy);
  }
  .info-text {
    position: absolute; left: 30px; top: 997px; width: 618px; text-align: center;
    color: var(--white); font-style: italic; font-weight: 400; font-size: 13.6px; line-height: 19.5px;
  }
  .info-text strong { color: var(--orange); font-weight: 700; }
  .cta {
    position: absolute; left: 137px; top: 1079px; width: 404px; height: 38px; border-radius: 19px;
    background: var(--orange); color: var(--white); font-weight: 700; font-size: 22px;
    line-height: 38px; text-align: center;
  }
  .address {
    position: absolute; left: 0; top: 1125px; width: 678px;
    font-weight: 500; font-size: 19px; line-height: 26px; color: var(--ink);
    display: flex; justify-content: center; align-items: center; gap: 6px;
  }
  .contact-line {
    position: absolute; left: 0; top: 1157px; width: 678px;
    display: flex; justify-content: center; gap: 16px;
    font-weight: 500; font-size: 13.5px; line-height: 18px; color: var(--ink);
  }
  .contact-item { display: flex; align-items: center; gap: 6px; }
</style>
</head>
<body>
<div class="flyer">

  <svg class="shape" width="678" height="240" viewBox="0 0 678 240" aria-hidden="true">
    <defs>
      <linearGradient id="topBand" x1="0" y1="0" x2="1" y2="0">
        <stop offset="0" stop-color="#0b6fae"/>
        <stop offset="1" stop-color="#1398d8"/>
      </linearGradient>
    </defs>
    <path d="M0,0 H678 V72 Q339,215 0,72 Z" fill="#36a9e0"/>
    <path d="M0,0 H678 V62 Q339,190 0,62 Z" fill="url(#topBand)"/>
    <path d="M0,74 Q339,222 678,74 L678,84 Q339,238 0,84 Z" fill="#f7923a"/>
  </svg>

  <div class="brand-badge">
    <span class="brand-name">Brookmere<br>Osteopathy</span>
  </div>

  <h1 class="headline-main">Osteopathy</h1>
  <p class="headline-script">that Cares</p>

  <svg class="shape" width="678" height="1000" viewBox="0 0 678 1000" aria-hidden="true">
    <defs>
      <linearGradient id="reasonsBand" x1="0" y1="0" x2="1" y2="0.3">
        <stop offset="0" stop-color="#1a86c4"/>
        <stop offset="0.6" stop-color="#14a2de"/>
        <stop offset="1" stop-color="#3cbdef"/>
      </linearGradient>
    </defs>
    <path d="M0,625 Q339,470 678,625 V981 H0 Z" fill="url(#reasonsBand)"/>
    <path d="M0,850 Q200,940 678,905 V981 H0 Z" fill="#1f7db8" opacity="0.35"/>
    <path d="M0,612 Q339,452 678,612 L678,620 Q339,472 0,625 Z" fill="#f7923a"/>
  </svg>

  <div class="photo photo-head"><div class="photo-fill" role="img" aria-label="Practitioner gently treating a woman's head and neck"></div></div>
  <div class="photo photo-baby"><div class="photo-fill" role="img" aria-label="Baby lying down receiving gentle cranial osteopathy"></div></div>
  <div class="photo photo-back"><div class="photo-fill" role="img" aria-label="Practitioner's hands treating a patient's upper back"></div></div>

  <h2 class="section-title">
    <span class="line-one">Common reasons</span>
    <span class="line-two">people visit an osteopath</span>
  </h2>
  <div class="divider"></div>

  <div class="reasons reasons-row-one">
    <div class="reason"><div class="reason-icon" role="img" aria-label="Line icon of a person with back and neck pain"></div><span class="reason-label">Back<br>/ neck pain</span></div>
    <div class="reason"><div class="reason-icon" role="img" aria-label="Line icon of a head with a headache"></div><span class="reason-label">Headaches<br>/ migraines</span></div>
    <div class="reason"><div class="reason-icon" role="img" aria-label="Line icon of a knee joint"></div><span class="reason-label">Joint and<br>muscle pain</span></div>
    <div class="reason"><div class="reason-icon" role="img" aria-label="Line icon of spinal vertebrae and discs"></div><span class="reason-label">Disc related<br>issues</span></div>
    <div class="reason"><div class="reason-icon" role="img" aria-label="Line icon of a hip and leg nerve"></div><span class="reason-label">Sciatica</span></div>
  </div>

  <div class="reasons reasons-row-two">
    <div class="reason"><div class="reason-icon" role="img" aria-label="Line icon of a pregnant belly"></div><span class="reason-label">Pregnancy<br>related<br>discomfort</span></div>
    <div class="reason"><div class="reason-icon" role="img" aria-label="Line icon of a foot"></div><span class="reason-label">Plantar<br>fasciitis</span></div>
    <div class="reason"><div class="reason-icon" role="img" aria-label="Line icon of a joint with tendon"></div><span class="reason-label">Tendonitis<br>/ Bursitis</span></div>
    <div class="reason"><div class="reason-icon" role="img" aria-label="Line icon of a medicine capsule"></div><span class="reason-label">Adhesive<br>capsulitis<br>(frozen shoulder)</span></div>
    <div class="reason"><div class="reason-icon" role="img" aria-label="Line icon of an elbow and racquet"></div><span class="reason-label">Tennis<br>/ Golfers<br>elbow</span></div>
  </div>

  <div class="info-band"></div>
  <p class="info-text">
    Osteopaths use a combination of <strong>joint manipulation</strong>, <strong>targeted deep</strong><br>
    <strong>tissue massage</strong> and <strong>stretching</strong> to improve <strong>function, relieve pain</strong> and<br>
    support the body’s ability to <strong>heal itself.</strong>
  </p>

  <div class="cta">Call us Today! 000-555-010</div>

  <p class="address">
    <svg width="14" height="19" viewBox="0 0 14 19" aria-hidden="true"><path d="M7,1 C3.7,1 1,3.6 1,6.9 C1,11 7,18 7,18 C7,18 13,11 13,6.9 C13,3.6 10.3,1 7,1 Z" fill="none" stroke="#f7923a" stroke-width="2"/><circle cx="7" cy="7" r="2.2" fill="#f7923a"/></svg>
    48 Old Mill road, Brookmere
  </p>

  <div class="contact-line">
    <span class="contact-item">
      <svg width="15" height="15" viewBox="0 0 16 16" aria-hidden="true"><g fill="none" stroke="#f7923a" stroke-width="1.2"><circle cx="8" cy="8" r="7"/><ellipse cx="8" cy="8" rx="3" ry="7"/><path d="M1,8 H15 M2,4.5 H14 M2,11.5 H14"/></g></svg>
      www.brookmereosteopathy.example
    </span>
    <span class="contact-item">
      <svg width="17" height="12" viewBox="0 0 17 12" aria-hidden="true"><g fill="none" stroke="#f7923a" stroke-width="1.2"><rect x="0.6" y="0.6" width="15.8" height="10.8"/><path d="M0.6,0.6 L8.5,7 L16.4,0.6"/></g></svg>
      info@brookmereosteopathy.example
    </span>
  </div>

</div>
</body>
</html>
```